New Business Card Design Project LORVANTI-Italy

we are LORVANTI-Italy
our company in the market for 3 years we are luxury cosmetic company and its about time for a facelift :)
i will like to have elegant luxurious and unique business card
that will give the person that get it a unique, luxurious and elegant impression
I'm VERY OPEN FOR NEW IDEAS , even duo i add a few files of things that i see on line and i like them

i add my logo as well
my website is LORVANTI.COM
(if you would like to see the main style that we have)

Target Market(s)

adult that have money :)

Industry/Entity Type

Business

Contact Information for Business Card

Name - Dario Lorvanti
Position - CEO and CO Founder
address - 4817 E Halvern
telephone - 555-384-1926
email - dario@lorvanti.com
fax - 555-384-1926
website - LORVANTI.COM

Colors
000000
959595
fbee3e
ffffff

Requirements
Must have
• big logo in GOLD color
• elegant look
• impressive
Nice to have
• not must but maybe classy pattern background
• not must but maybe emblem
• maybe clear plastic business card
Should not have
• colors
• images

```html
<!DOCTYPE html>
<html lang="en">
<head>
<meta charset="utf-8">
<title>LORVANTI Italy – Business Card</title>
<link rel="stylesheet" href="https://fonts.googleapis.com/css2?family=Cinzel:wght@500;700&family=Open+Sans:wght@400&display=swap">
<style>
  :root {
    --page: #ffffff;
    --card-top: #17181c;
    --card-mid: #1f2024;
    --card-bottom: #36373b;
    --gold: #d6ab3c;
    --gold-soft: #e9c35a;
    --text-light: #f4f4f4;
    --icon-ink: #1d1d20;
  }
  * { margin: 0; padding: 0; box-sizing: border-box; }
  html, body {
    width: 1200px; height: 900px; overflow: hidden;
    background: var(--page);
  }
  .canvas { position: relative; width: 1200px; height: 900px; }

  .card {
    position: absolute; top: 184px; height: 491px;
    border-radius: 14px;
    background: linear-gradient(165deg, var(--card-top) 0%, var(--card-mid) 55%, var(--card-bottom) 100%);
    overflow: hidden;
  }
  .card--front { left: 299px; width: 301px; }
  .card--back  { left: 645px; width: 305px; }

  .brand-mark {
    position: absolute; border-radius: 50%;
    border: 3px solid var(--gold);
  }
  .brand-name, .brand-country {
    position: absolute; left: 0; right: 0; text-align: center;
    font-family: "Cinzel", serif; font-weight: 500; color: var(--gold);
    line-height: 1;
  }

  .card--front .brand-mark { left: 109px; top: 52px; width: 82px; height: 82px; }
  .card--front .brand-name { top: 152px; font-size: 33px; letter-spacing: 0.5px; }
  .card--front .brand-country { top: 198px; font-size: 15px; letter-spacing: 0.5px; }

  .card--back .brand-mark { left: 99px; top: 141px; width: 106px; height: 106px; }
  .card--back .brand-name { top: 272px; font-size: 45px; letter-spacing: 0.5px; }
  .card--back .brand-country { top: 335px; font-size: 18px; letter-spacing: 0.5px; }

  .person { position: absolute; left: 32px; top: 263px; }
  .person__name {
    font-family: "Cinzel", serif; font-weight: 700; font-size: 21px;
    color: var(--gold); line-height: 1;
  }
  .person__role {
    margin-top: 7px;
    font-family: "Open Sans", sans-serif; font-size: 13px; color: var(--text-light);
  }

  .contact-list { position: absolute; left: 32px; top: 325px; list-style: none; }
  .contact-list li {
    display: flex; align-items: center; gap: 6px;
    height: 22.5px;
    font-family: "Open Sans", sans-serif; font-size: 13px; color: var(--text-light);
  }
  .contact-icon { width: 16px; height: 16px; flex: none; }

  .address {
    position: absolute; left: 32px; top: 430px;
    font-family: "Open Sans", sans-serif; font-size: 13px; color: var(--text-light);
  }
</style>
</head>
<body>
<main class="canvas">

  <section class="card card--front" aria-label="Business card front">
    <div class="brand-mark"></div>
    <div class="brand-name">LORVANTI</div>
    <div class="brand-country">ITALY</div>

    <div class="person">
      <div class="person__name">DARIO LORVANTI</div>
      <div class="person__role">CEO and CO Founder</div>
    </div>

    <ul class="contact-list">
      <li>
        <svg class="contact-icon" viewBox="0 0 16 16" aria-hidden="true">
          <circle cx="8" cy="8" r="8" fill="var(--gold-soft)"/>
          <path d="M4.5 6.5c0-1.2 1.6-2 3.5-2s3.5.8 3.5 2v.6H9.8v-.8H6.2v.8H4.5z M5.5 8h5l.8 3.5H4.7z" fill="var(--icon-ink)"/>
        </svg>
        555-384-1926
      </li>
      <li>
        <svg class="contact-icon" viewBox="0 0 16 16" aria-hidden="true">
          <circle cx="8" cy="8" r="8" fill="var(--gold-soft)"/>
          <rect x="5.5" y="4" width="5" height="3" fill="none" stroke="var(--icon-ink)" stroke-width="1"/>
          <rect x="4.5" y="7" width="7" height="5" rx="0.8" fill="var(--icon-ink)"/>
        </svg>
        555-384-1926
      </li>
      <li>
        <svg class="contact-icon" viewBox="0 0 16 16" aria-hidden="true">
          <circle cx="8" cy="8" r="8" fill="var(--gold-soft)"/>
          <rect x="4" y="5.2" width="8" height="5.6" rx="0.6" fill="var(--icon-ink)"/>
          <path d="M4.3 5.6 8 8.4l3.7-2.8" fill="none" stroke="var(--gold-soft)" stroke-width="0.9"/>
        </svg>
        dario@lorvanti.com
      </li>
      <li>
        <svg class="contact-icon" viewBox="0 0 16 16" aria-hidden="true">
          <circle cx="8" cy="8" r="8" fill="var(--gold-soft)"/>
          <circle cx="8" cy="8" r="4" fill="none" stroke="var(--icon-ink)" stroke-width="1.2"/>
          <path d="M4 8h8M8 4c-1.6 1.2-1.6 6.8 0 8M8 4c1.6 1.2 1.6 6.8 0 8" fill="none" stroke="var(--icon-ink)" stroke-width="0.9"/>
        </svg>
        LORVANTI.COM
      </li>
    </ul>

    <div class="address">4817 E Halvern</div>
  </section>

  <section class="card card--back" aria-label="Business card back">
    <div class="brand-mark"></div>
    <div class="brand-name">LORVANTI</div>
    <div class="brand-country">ITALY</div>
  </section>

</main>
</body>
</html>
```